Business card for Luxury Portable Restroom Trailer company

We are a Luxury Portable Restroom Trailer Company Called FALCRIDGE HIRES. Based in Orange County California. We provide portable restroom trailers for events, such as, Weddings, Concerts, Charity events, Sporting events, Tournaments, Corporate events, ect. We rent and Sell the Luxury restrooms. Our colors are white, grey, and Orange. As you will see in the logo we uploaded.
There are 2 people in the company so the names and titles will change for the 3 people but card will remain the same. Here is the information for each Person: Dwight Penner CFO 555 318-0476
next Person: Leon Marchetti VP 555 318-0476
Next Person: Owen Marchetti CEO 555 318-0476
Information to include on the card: Luxury Restroom Trailers Rental and Sales. Weddings, Concerts, Charity, Sporting and Corp. Events.

```html
<!DOCTYPE html>
<html lang="en">
<head>
<meta charset="UTF-8">
<title>Falcridge Hires – Business Card</title>
<link rel="stylesheet" href="https://fonts.googleapis.com/css2?family=Montserrat:wght@400;500;700;800&display=swap">
<style>
  :root {
    --orange: #f26a21;
    --grey: #58595b;
    --ink: #2b2b2b;
    --paper: #ffffff;
    --backdrop: #e6e6e8;
  }
  * { margin: 0; padding: 0; box-sizing: border-box; }
  html, body { width: 1200px; height: 900px; overflow: hidden; }
  body {
    background: var(--backdrop);
    font-family: "Montserrat", Arial, sans-serif;
    position: relative;
  }
  .card {
    position: absolute;
    left: 320px;
    width: 560px;
    height: 320px;
    background: var(--paper);
    border-radius: 18px;
    overflow: hidden;
    box-shadow: 0 10px 30px rgba(0,0,0,0.15);
  }
  .card--front { top: 100px; }
  .card--back { top: 480px; }

  .brand {
    display: flex;
    align-items: center;
    gap: 12px;
    color: var(--orange);
    font-weight: 800;
    letter-spacing: 1px;
    white-space: nowrap;
  }
  .brand__mark {
    background: var(--orange);
    flex: none;
  }
  .card--front .brand {
    position: absolute;
    left: 50%; top: 50%;
    transform: translate(-50%, -60%);
    font-size: 38px;
  }
  .card--front .brand__mark { width: 30px; height: 30px; }

  .edge-bar {
    position: absolute;
    left: 0; right: 0; bottom: 0;
    height: 9px;
    display: flex;
  }
  .edge-bar__orange { flex: 0 0 58%; background: var(--orange); }
  .edge-bar__grey { flex: 1; background: var(--grey); }

  .card--back .brand {
    position: absolute;
    left: 36px; top: 118px;
    font-size: 21px;
    gap: 8px;
  }
  .card--back .brand__mark { width: 16px; height: 16px; }

  .divider {
    position: absolute;
    left: 290px; top: 40px;
    width: 1.5px; height: 190px;
    background: var(--orange);
  }

  .contact {
    position: absolute;
    left: 312px; top: 34px;
    color: var(--ink);
    font-size: 11.5px;
    line-height: 1.45;
  }
  .contact__name {
    color: var(--orange);
    font-weight: 700;
    font-size: 19px;
    line-height: 1.1;
  }
  .contact__title { font-weight: 500; margin-bottom: 8px; }
  .contact__address { margin-bottom: 8px; }
  .contact__list { list-style: none; }
  .contact__list li { display: flex; align-items: center; gap: 8px; }
  .contact__list svg { width: 12px; height: 12px; flex: none; }

  .services-band {
    position: absolute;
    left: 0; right: 0; bottom: 22px;
    height: 36px;
    background: var(--orange);
    color: var(--paper);
    font-size: 11.5px;
    letter-spacing: 0.4px;
    display: flex;
    align-items: center;
    justify-content: center;
    white-space: nowrap;
  }
</style>
</head>
<body>

  <section class="card card--front" aria-label="Card front">
    <div class="brand">
      <span class="brand__mark"></span>
      <span class="brand__name">FALCRIDGE HIRES</span>
    </div>
    <div class="edge-bar">
      <span class="edge-bar__orange"></span>
      <span class="edge-bar__grey"></span>
    </div>
  </section>

  <section class="card card--back" aria-label="Card back">
    <div class="brand">
      <span class="brand__mark"></span>
      <span class="brand__name">FALCRIDGE HIRES</span>
    </div>

    <span class="divider"></span>

    <div class="contact">
      <p class="contact__name">Owen Marchetti</p>
      <p class="contact__title">CEO</p>
      <p class="contact__address">418 Harbor View Ave, #112<br>Costa Mesa, CA 92626</p>
      <ul class="contact__list">
        <li>
          <svg viewBox="0 0 24 24" fill="var(--orange)"><path d="M6.6 10.8a15 15 0 0 0 6.6 6.6l2.2-2.2c.3-.3.7-.4 1-.2 1.1.4 2.3.6 3.6.6.6 0 1 .4 1 1V20c0 .6-.4 1-1 1A17 17 0 0 1 3 4c0-.6.4-1 1-1h3.5c.6 0 1 .4 1 1 0 1.3.2 2.5.6 3.6.1.3 0 .7-.2 1z"/></svg>
          555 318-0476
        </li>
        <li>
          <svg viewBox="0 0 24 24" fill="none" stroke="var(--orange)" stroke-width="2.2"><rect x="6" y="2" width="12" height="20" rx="2"/><line x1="11" y1="18" x2="13" y2="18"/></svg>
          555 318-0476
        </li>
        <li>
          <svg viewBox="0 0 24 24" fill="var(--orange)"><path d="M2 5h20v14H2z M2 5l10 8 10-8" stroke="#fff" stroke-width="1.5"/></svg>
          info@falcridgehires.com
        </li>
        <li>
          <svg viewBox="0 0 24 24" fill="none" stroke="var(--orange)" stroke-width="2.2"><circle cx="12" cy="12" r="9"/><path d="M3 12h18M12 3c3 3 3 15 0 18M12 3c-3 3-3 15 0 18"/></svg>
          www.falcridgehires.com
        </li>
      </ul>
    </div>

    <div class="services-band">
      LUXURY TOILET RENTALS &nbsp;•&nbsp; WEDDINGS &nbsp;•&nbsp; CONCERTS &nbsp;•&nbsp; PARTIES AND EVENTS
    </div>
  </section>

</body>
</html>
```